Dusty Spur Outfitters Home Page

I need a logo and page design for my home page, maybe some background color suggestions to go with it. I want the logo to project "vintage" and "western wear" but not be your typical trite western saddle and gun type thing.
http://www.dustyspuroutfitters.example/store/cart.php
Not looking for page coding just logo and other design elements to lay in over the site's template to make it "pop"
Reason: Have to finalize the design.
Target Market(s)
My customers are 70/30 men to women.
Industry/Entity Type
Gun

```html
<!DOCTYPE html>
<html lang="en">
<head>
<meta charset="utf-8">
<title>Dusty Spur Outfitters</title>
<link rel="stylesheet" href="https://fonts.googleapis.com/css2?family=Rye&family=Lato:wght@400;700&family=Oswald:wght@500&family=Dancing+Script:wght@500&display=swap">
<style>
  :root {
    --bar: #d9ccb3;
    --band: #2b2a29;
    --canvas: #cdbc9f;
    --ink: #3a3532;
    --paper: #e8dcc4;
    --muted: #8a8784;
    --accent: #b5261f;
    --sky: #8fc4dd;
    --tile: #8fd3e6;
    --frame: #e6dac2;
  }
  * { margin: 0; padding: 0; box-sizing: border-box; }
  html, body { width: 1200px; height: 664px; overflow: hidden; }
  body {
    position: relative;
    background: var(--canvas);
    font-family: "Lato", sans-serif;
    color: var(--ink);
  }
  .topbar {
    position: absolute; left: 0; top: 0; width: 1200px; height: 35px;
    background: var(--bar);
    font-family: "Oswald", sans-serif; font-size: 14px; letter-spacing: .1px;
    text-transform: uppercase; color: var(--ink);
  }
  .topbar a { color: inherit; text-decoration: none; }
  .nav-main { position: absolute; left: 38px; top: 4px; display: flex; gap: 11px; }
  .nav-help { position: absolute; left: 823px; top: 5px; display: flex; gap: 12px; }
  .nav-icons { position: absolute; left: 1099px; top: 6px; display: flex; gap: 12px; }
  .header {
    position: absolute; left: 0; top: 35px; width: 1200px; height: 110px;
    background: var(--band);
    box-shadow: 0 2px 4px rgba(0,0,0,.35);
  }
  .brand {
    position: absolute; left: 39px; top: 36px; width: 270px;
    font-family: "Rye", serif; font-size: 25px; line-height: 1.15;
    color: var(--paper); text-align: center;
  }
  .tagline {
    position: absolute; left: 340px; top: 28px; width: 598px;
    font-family: "Dancing Script", cursive; font-weight: 500; font-size: 24px; line-height: 29px;
    color: var(--muted); text-align: right;
  }
  .search { position: absolute; left: 1000px; top: 45px; display: flex; align-items: center; gap: 7px; }
  .field {
    width: 113px; height: 19px; border-radius: 10px; background: var(--paper);
    font-size: 11.5px; font-weight: 700; padding: 3px 11px; color: var(--ink);
  }
  .go { font-size: 12px; font-weight: 700; color: var(--paper); }
  .sidebar { position: absolute; left: 38px; top: 170px; width: 200px; }
  .sidebar h2 { font-family: "Rye", serif; font-weight: 400; color: var(--ink); }
  .message { font-size: 17px; margin-left: 3px; }
  .newsletter { font-size: 17px; margin-top: 21px; text-transform: none; }
  .signup { display: flex; align-items: center; gap: 6px; margin-top: 8px; }
  .signup .field { width: 115px; background: var(--band); color: var(--accent); font-size: 11px; box-shadow: inset 0 0 0 1px #55504b; }
  .signup .go { color: var(--accent); }
  .list-title { font-size: 13px; margin-top: 38px; }
  .links { list-style: none; margin-top: 8px; font-size: 11px; font-weight: 700; line-height: 13px; }
  .links.info { margin-top: 9px; }
  .info-title { margin-top: 24px; }
  .slider {
    position: absolute; left: 245px; top: 153px; width: 695px; height: 278px;
    background: var(--frame); padding: 4px;
    box-shadow: 1px 2px 3px rgba(0,0,0,.4);
  }
  .slide-photo { position: relative; width: 100%; height: 100%; background: linear-gradient(120deg, #a7a9ae 0%, #8ec4de 40%, #79b7d6 100%); }
  .slide-label {
    position: absolute; right: 9px; bottom: 3px;
    font-family: "Rye", serif; font-size: 25px; color: #f4ede0;
  }
  .dots { position: absolute; left: 578px; top: 454px; display: flex; gap: 10px; }
  .dots span { width: 8px; height: 8px; border-radius: 50%; border: 1.5px solid var(--ink); }
  .dots span.on { background: var(--ink); }
  .featured {
    position: absolute; left: 245px; top: 486px;
    font-family: "Rye", serif; font-weight: 400; font-size: 28px; color: var(--ink);
  }
  .products { position: absolute; left: 262px; top: 549px; display: flex; gap: 46px; }
  .product { width: 130px; height: 140px; background: var(--frame); padding: 3px; box-shadow: 1px 1px 2px rgba(0,0,0,.35); }
  .product div { width: 100%; height: 100%; }
  .cart { position: absolute; left: 981px; top: 157px; width: 178px; }
  .cart h2 { font-family: "Rye", serif; font-weight: 400; font-size: 16px; text-align: center; color: var(--ink); }
  .cart-box {
    margin-top: 7px; height: 93px; background: var(--band); border: 1px solid var(--paper);
    padding: 8px 9px; color: var(--paper); font-size: 12px; font-weight: 700;
  }
  .subtotal { display: flex; justify-content: space-between; }
  .btn {
    display: block; width: 114px; height: 19px; margin: 8px auto 0; border-radius: 10px;
    background: var(--paper); color: var(--ink); text-align: center; line-height: 19px; font-size: 12px;
  }
</style>
</head>
<body>
  <div class="topbar">
    <nav class="nav-main">
      <a href="#">Men's Western Wear</a><a href="#">Women's Western Wear</a><a href="#">New Arrivals!</a><a href="#">Boots</a>
    </nav>
    <nav class="nav-help"><a href="#">Sizing Charts</a><a href="#">Help</a></nav>
    <div class="nav-icons">
      <svg width="20" height="16" viewBox="0 0 20 16" aria-label="Account"><circle cx="6" cy="4" r="3.5" fill="#3a3532"/><path d="M0 15c0-5 2.5-6.5 6-6.5s6 1.5 6 6.5z" fill="#3a3532"/><path d="M14 10l2.5 2.5L19 10" stroke="#3a3532" stroke-width="1.6" fill="none"/></svg>
      <svg width="30" height="16" viewBox="0 0 30 16" aria-label="Cart"><path d="M0 1h4l3 9h11l2-6H6" stroke="#3a3532" stroke-width="2" fill="none"/><rect x="6" y="4" width="13" height="5" fill="#3a3532"/><circle cx="8" cy="13.5" r="1.6" fill="#3a3532"/><circle cx="17" cy="13.5" r="1.6" fill="#3a3532"/><path d="M24 10l2.5 2.5L29 10" stroke="#3a3532" stroke-width="1.6" fill="none"/></svg>
    </div>
  </div>

  <header class="header">
    <div class="brand">Dusty Spur Outfitters</div>
    <p class="tagline">Internet's best selection and value for brand new Retro-Styled Vintage Western&nbsp; fashions for Men and Women</p>
    <div class="search"><div class="field">Search...</div><span class="go">GO!</span></div>
  </header>

  <aside class="sidebar">
    <h2 class="message">LEAVE US A MESSAGE!</h2>
    <h2 class="newsletter">Join our Newsletter!</h2>
    <div class="signup"><div class="field">Email</div><span class="go">GO!</span></div>
    <h2 class="list-title">CATEGORIES</h2>
    <ul class="links">
      <li>Men's Western Wear</li><li>Women's Western Wear</li><li>Boots</li><li>Accessories</li><li>Belts</li><li>Big and tall</li><li>Brand New Arrivals</li><li>CLEARANCE</li><li>Handbags</li><li>Jackets</li><li>Jeans</li><li>Leather</li><li>ON Sale</li><li>Pants</li><li>Short Sleeves</li><li>T-Shirts</li><li>Vests</li>
    </ul>
    <h2 class="list-title info-title">INFORMATION</h2>
    <ul class="links info">
      <li>About Us</li><li>Contact Us</li><li>Privacy Policy</li><li>Shipping and Returns</li><li>Sizing Charts</li>
    </ul>
  </aside>

  <section class="slider">
    <div class="slide-photo" role="img" aria-label="Back of a light blue western shirt with dark embroidered scrollwork across the yoke">
      <span class="slide-label">NEW ARRIVALS</span>
    </div>
  </section>
  <div class="dots"><span></span><span class="on"></span></div>

  <h2 class="featured">FEATURED PRODUCTS</h2>
  <div class="products">
    <div class="product"><div role="img" aria-label="Man in a black embroidered western shirt" style="background:linear-gradient(180deg,#6fd6ea 0%,#3b3f44 60%)"></div></div>
    <div class="product"><div role="img" aria-label="Man in a cream western shirt with sky blue yoke" style="background:linear-gradient(180deg,#9fd3e6 0%,#e6dcc8 60%)"></div></div>
    <div class="product"><div role="img" aria-label="Man in a black hat and burgundy vest" style="background:linear-gradient(180deg,#9fd3e6 0%,#6a2c2c 65%)"></div></div>
    <div class="product"><div role="img" aria-label="Man in a brown hat and patterned vest" style="background:linear-gradient(180deg,#9fd3e6 0%,#7a6750 65%)"></div></div>
  </div>

  <aside class="cart">
    <h2>SHOPPING CART</h2>
    <div class="cart-box">
      <div class="subtotal"><span>Subtotal:</span><span>$ 0.00</span></div>
      <span class="btn">Update Cart</span>
      <span class="btn">Checkout</span>
    </div>
  </aside>
</body>
</html>
```